Coffeeshop menu for filter tip

We want to have a cannabis (coffeeshop) menu in the size 25mm wide x 60mm wide. Some examples attached.

it must have the following text:
Menu

WEED p/g
Oblivane €16
Cloudplum €14
Tide Runner €14
Quincefig €16
Mega Marsh €14
Grey Heron €14

HASH p/g
Tashar Amber €12
Pebble Frost€11
Lime Dunes €14
Ash Petal €10

Target Market(s)

tourist in Amsterdam

Requirements
Nice to have
• cannabis sign leaf
• No Cigarettes allowed symbol

```html
<!DOCTYPE html>
<html lang="en">
<head>
<meta charset="utf-8">
<title>Coffeeshop Menu</title>
<link rel="stylesheet" href="https://fonts.googleapis.com/css2?family=Questrial&display=swap">
<style>
  :root {
    --bg: #0d0d0d;
    --leaf-shade: #1c1d1c;
    --weed-panel: #1a1b1a;
    --hash-panel: #050505;
    --footer: #000000;
    --accent: #fff25a;
    --light: #ffffff;
    --skyline-top: #2a2a2a;
    --skyline-bottom: #121212;
  }
  * { margin: 0; padding: 0; box-sizing: border-box; }
  html, body { width: 1200px; height: 2880px; overflow: hidden; background: var(--bg); }
  .menu {
    position: relative;
    width: 1200px;
    height: 2880px;
    overflow: hidden;
    font-family: "Questrial", sans-serif;
    background: var(--bg);
  }
  .backdrop {
    position: absolute;
    inset: 0;
    background:
      radial-gradient(ellipse 520px 700px at 1000px 200px, var(--leaf-shade), transparent 70%),
      radial-gradient(ellipse 420px 900px at 60px 1200px, var(--leaf-shade), transparent 70%),
      radial-gradient(ellipse 600px 500px at 1000px 1700px, #161716, transparent 70%);
  }
  .notice {
    position: absolute;
    top: 42px;
    left: 216px;
    display: flex;
    align-items: center;
    gap: 26px;
    color: var(--light);
    font-size: 58px;
    letter-spacing: 15px;
    line-height: 1;
    text-transform: uppercase;
  }
  .notice svg { width: 68px; height: 68px; }
  .heading {
    position: absolute;
    display: flex;
    justify-content: space-between;
    color: var(--accent);
    font-size: 128px;
    line-height: 1;
    text-transform: uppercase;
  }
  .heading--weed { top: 176px; left: 436px; width: 712px; }
  .heading--hash { top: 1536px; left: 62px; width: 674px; }
  .panel { position: absolute; }
  .panel--weed { left: 163px; top: 328px; width: 1037px; height: 1120px; background: var(--weed-panel); }
  .panel--hash { left: 0; top: 1675px; width: 1051px; height: 765px; background: var(--hash-panel); }
  .item {
    position: absolute;
    left: 0;
    right: 0;
    height: 110px;
    font-size: 98px;
    line-height: 110px;
    white-space: nowrap;
  }
  .item__name { position: absolute; color: var(--accent); text-transform: uppercase; }
  .item__price { position: absolute; color: var(--light); letter-spacing: -3px; }
  .panel--weed .item__name { left: 48px; }
  .panel--weed .item__price { right: 27px; }
  .panel--hash .item__price { left: 35px; }
  .panel--hash .item__name { left: 240px; }
  .skyline {
    position: absolute;
    left: 0;
    top: 2440px;
    width: 1200px;
    height: 216px;
    background: linear-gradient(var(--skyline-top), var(--skyline-bottom));
  }
  .footer {
    position: absolute;
    left: 0;
    top: 2656px;
    width: 1200px;
    height: 224px;
    background: var(--footer);
  }
  .footer__title {
    position: absolute;
    top: 50px;
    left: 246px;
    width: 712px;
    display: flex;
    justify-content: space-between;
    color: var(--light);
    font-size: 140px;
    line-height: 1;
    text-transform: uppercase;
  }
</style>
</head>
<body>
<main class="menu">
  <div class="backdrop" role="img" aria-label="Faint cannabis leaf illustrations on a dark background"></div>

  <p class="notice">No cigarettes
    <svg viewBox="0 0 40 40" aria-hidden="true">
      <circle cx="20" cy="20" r="17" fill="none" stroke="#fff" stroke-width="3"/>
      <rect x="9" y="19" width="20" height="4" fill="#fff"/>
      <line x1="8" y1="8" x2="32" y2="32" stroke="#fff" stroke-width="3"/>
    </svg>
  </p>

  <h2 class="heading heading--weed"><span>W</span><span>E</span><span>E</span><span>D</span></h2>
  <section class="panel panel--weed">
    <div class="item" style="top:84px"><span class="item__name">Oblivane</span><span class="item__price">€16</span></div>
    <div class="item" style="top:260px"><span class="item__name">Cloudplum</span><span class="item__price">€14</span></div>
    <div class="item" style="top:436px"><span class="item__name">Tide Runner</span><span class="item__price">€14</span></div>
    <div class="item" style="top:612px"><span class="item__name">Quincefig</span><span class="item__price">€16</span></div>
    <div class="item" style="top:788px"><span class="item__name">Mega Marsh</span><span class="item__price">€14</span></div>
    <div class="item" style="top:964px"><span class="item__name">Grey Heron</span><span class="item__price">€14</span></div>
  </section>

  <h2 class="heading heading--hash"><span>H</span><span>A</span><span>S</span><span>H</span></h2>
  <section class="panel panel--hash">
    <div class="item" style="top:83px"><span class="item__price">€12</span><span class="item__name">Tashar Amber</span></div>
    <div class="item" style="top:259px"><span class="item__price">€11</span><span class="item__name">Pebble Frost</span></div>
    <div class="item" style="top:435px"><span class="item__price">€14</span><span class="item__name">Lime Dunes</span></div>
    <div class="item" style="top:611px"><span class="item__price">€10</span><span class="item__name">Ash Petal</span></div>
  </section>

  <div class="skyline" role="img" aria-label="Silhouette of the Amsterdam skyline"></div>

  <footer class="footer">
    <h1 class="footer__title"><span>M</span><span>E</span><span>N</span><span>U</span></h1>
  </footer>
</main>
</body>
</html>
```